New Zealand Marlborough Sauvignon Blanc wine packaging design

We need packaging design for our new wine brand, Dunmore Vale. The wine is a New Zealand Marlborough Sauvignon Blanc. We would like the packaging will portray elegance and style with an understated label. We are looking for a label that portrays the elegance of the French Riviera. The label should be round or pill shaped.
Updates

Industry/Entity Type

Wine

Font styles to use
Serif
Sans Serif

Requirements
Must have
• The words in order of importance: Dunmore Vale, Sauvignon Blanc, Marlborough, New Zealand. It should be fit to the bottle posted in the links
Nice to have
• a pill shape or circular shape
Should not have
• Illustrations of wine bottles, wine glasses, or grapes

```html
<!DOCTYPE html>
<html lang="en">
<head>
<meta charset="utf-8">
<title>Dunmore Vale Sauvignon Blanc Label</title>
<link rel="stylesheet" href="https://fonts.googleapis.com/css2?family=League+Spartan:wght@700;800&display=swap">
<style>
  :root {
    --lime: #97c01f;
    --lime-pale: #bdd65e;
    --paper: #ffffff;
  }
  html, body {
    margin: 0;
    padding: 0;
    width: 1200px;
    height: 675px;
    overflow: hidden;
    background: var(--paper);
  }
  .canvas {
    position: relative;
    width: 1200px;
    height: 675px;
    display: flex;
    align-items: center;
    justify-content: center;
  }
  .wine-label {
    display: block;
    width: 360px;
    height: 527px;
  }
  .wine-label text {
    font-family: "League Spartan", "Helvetica Neue", Arial, sans-serif;
  }
  .brand-primary { fill: var(--paper); font-weight: 800; }
  .brand-secondary { fill: var(--lime); font-weight: 800; }
  .varietal { fill: var(--lime-pale); font-weight: 800; }
  .region { fill: var(--paper); font-weight: 700; }
  .pill-body { fill: var(--lime); }
  .pill-keyline { fill: none; stroke: var(--paper); stroke-width: 8; }
  .name-band { fill: var(--paper); }
  .map-area { fill: var(--paper); opacity: 0.35; }
</style>
</head>
<body>
<main class="canvas">
  <svg class="wine-label" viewBox="258 160 772 1130" xmlns="http://www.w3.org/2000/svg" aria-label="Dunmore Vale Sauvignon Blanc, Marlborough, New Zealand">
    <rect class="pill-body" x="258" y="160" width="772" height="1130" rx="386" ry="386"/>
    <rect class="pill-keyline" x="316" y="218" width="656" height="1014" rx="328" ry="328"/>

    <rect class="name-band" x="565" y="220" width="150" height="1035"/>

    <text class="brand-primary" transform="translate(565,1190) rotate(-90)" font-size="200" textLength="960" lengthAdjust="spacingAndGlyphs">DUNMORE</text>
    <text class="brand-secondary" transform="translate(715,1250) rotate(-90)" font-size="205" textLength="590" lengthAdjust="spacingAndGlyphs">VALE</text>

    <text class="varietal" transform="translate(640,625) rotate(-90)" font-size="86" textLength="390" lengthAdjust="spacingAndGlyphs">SAUVIGNON</text>
    <text class="varietal" transform="translate(697,625) rotate(-90)" font-size="86" textLength="220" lengthAdjust="spacingAndGlyphs">BLANC</text>

    <text class="region" x="722" y="808" font-size="24" textLength="172" lengthAdjust="spacingAndGlyphs">MARLBOROUGH,</text>
    <text class="region" x="722" y="826" font-size="24" textLength="157" lengthAdjust="spacingAndGlyphs">NEW ZEALAND</text>

    <rect class="map-area" x="720" y="680" width="300" height="410" rx="40" ry="40" role="img" aria-label="Map outline of New Zealand"/>
  </svg>
</main>
</body>
</html>
```